Website Redesign

This is a B2B (Mainly)/B2C website .

Vaporel (our manufacturer) only sells the Sprayer itself. As a result they rarely speak directly to the benefits of a disinfecting chemicals ie. Their marketing is more directed to how quickly the sprayer can cover a given area or how much disinfecting Chemical is saved by spraying instead of the 'spray and wipe method. Also how much labor is saved by spraying.

We will be selling both similar to brindlowash.com

1. Main Selling Point? Infectious disease control and prevention via Electromagnetic Disinfecting Sprayers. Upsell is chemicals used in the sprayer and other products for use in disinfection and cleaning.

Our price point is $1495 so sales generally happen after they speak to our sales team.

End user is in most cases a Business. In some cases an individual as well but 75% business, hospital, School district, Universities.

Redesign is meant to tell a much better story to customer by and presenting a cleaner design. Most important metric is increased conversions.

Number of Pages Required

5+ page

```html
<!DOCTYPE html>
<html lang="en">
<head>
<meta charset="utf-8">
<title>Halvix Group</title>
<link href="https://fonts.googleapis.com/css2?family=Montserrat:wght@400;500;600&family=Open+Sans:wght@400;600&display=swap" rel="stylesheet">
<style>
:root{
  --blue:#1a72c0;
  --blue-dark:#135da0;
  --ink:#2f2f33;
  --muted:#555b62;
  --soft:#f3f3f5;
  --line:#e2e4e8;
  --white:#ffffff;
  --footer:#2a2a2c;
}
*{margin:0;padding:0;box-sizing:border-box}
html,body{width:1200px;height:4055px;overflow:hidden;background:var(--white)}
body{position:relative;font-family:"Open Sans",Arial,sans-serif;color:var(--ink)}
.head{font-family:"Montserrat",Arial,sans-serif}
.abs{position:absolute}
.center{text-align:center;left:0;width:1200px}
.btn{position:absolute;display:flex;align-items:center;justify-content:center;background:var(--blue);color:var(--white);font-family:"Montserrat",Arial,sans-serif;font-weight:500;border-radius:30px;text-transform:uppercase}
.accent{color:var(--blue)}

/* header */
.site-header{top:0;left:0;width:1200px;height:109px;background:var(--white)}
.brand{left:112px;top:36px;font-family:"Montserrat",sans-serif;font-size:34px;font-weight:500;color:var(--blue);letter-spacing:.5px}
.nav a{position:absolute;top:48px;font-family:"Montserrat",sans-serif;font-size:13px;font-weight:500;color:var(--ink);text-decoration:none;text-transform:uppercase}
.nav a.active{color:var(--blue)}

/* hero */
.hero{top:109px;left:0;width:1200px;height:663px;background:linear-gradient(100deg,#c9b6a4 0%,#b77c52 30%,#8b6a6c 55%,#4d6a9a 80%,#3d5e8e 100%)}
.hero-shade{top:109px;left:0;width:1200px;height:663px;background:rgba(20,30,60,.18)}
.hero-title{top:370px;font-family:"Montserrat",sans-serif;font-size:78px;font-weight:500;color:var(--white);letter-spacing:1px}
.hero-sub{top:485px;font-family:"Montserrat",sans-serif;font-size:20px;font-weight:500;color:var(--white);text-transform:uppercase}
.dots{top:745px;left:576px;display:flex;gap:7px}
.dots span{width:11px;height:11px;border-radius:50%;background:var(--white)}
.dots span.on{background:var(--blue)}

/* welcome */
.welcome{top:772px;left:0;width:1200px;height:370px;background:var(--soft)}
.section-title{font-family:"Montserrat",sans-serif;font-size:32px;font-weight:500;color:var(--ink);text-transform:uppercase}
.welcome-text{top:888px;left:237px;width:726px;text-align:center;font-size:13px;line-height:30px;color:var(--muted)}

/* products */
.rule{height:3px;width:60px;background:var(--blue)}
.card{position:absolute;top:1285px;width:310px;height:460px;background:var(--white);box-shadow:0 0 6px rgba(0,0,0,.16)}
.card .photo{position:absolute;top:0;left:0;width:310px;height:295px;background:radial-gradient(circle at 50% 50%,#5b5e63 0%,#2c2d31 35%,#ffffff 62%)}
.card .name{position:absolute;top:308px;width:100%;text-align:center;font-family:"Montserrat",sans-serif;font-size:22px;color:var(--ink)}
.card .price{position:absolute;top:340px;width:100%;text-align:center;font-family:"Montserrat",sans-serif;font-size:24px;font-weight:600;color:var(--blue)}
.card .btn{top:380px;left:78px;width:155px;height:50px;font-size:14px}

/* features */
.feature-img{position:absolute;height:333px;width:488px}
.feature-title{position:absolute;font-family:"Montserrat",sans-serif;font-size:24px;font-weight:500;line-height:35px;color:var(--ink)}
.feature-rule{position:absolute;height:3px;width:42px;background:var(--blue)}
.feature-text{position:absolute;width:425px;font-size:14px;line-height:30px;color:var(--muted);text-align:justify}
.read-more{position:absolute;font-family:"Montserrat",sans-serif;font-size:16px;font-weight:600;color:var(--blue);text-decoration:underline;display:flex;align-items:center;gap:8px}

/* video band */
.band{top:2611px;left:0;width:1200px;height:435px;background:linear-gradient(120deg,#2b78c4 0%,#1f6fbf 45%,#3c86cb 100%)}
.band-title{top:2723px;font-family:"Montserrat",sans-serif;font-size:34px;font-weight:500;line-height:50px;color:var(--white)}

/* audience */
.aud{position:absolute;top:3120px;width:234px;height:290px;background:var(--white);box-shadow:0 0 6px rgba(0,0,0,.16)}
.aud .icon{position:absolute;top:19px;left:56px;width:122px;height:122px;border-radius:50%;background:var(--blue);display:flex;align-items:center;justify-content:center}
.aud h3{position:absolute;top:155px;width:100%;text-align:center;font-family:"Montserrat",sans-serif;font-size:22px;font-weight:500;color:var(--ink)}
.aud p{position:absolute;top:190px;left:14px;width:206px;text-align:center;font-size:12.5px;line-height:26px;color:var(--muted)}

/* contact */
.contact{top:3473px;left:0;width:1200px;height:501px;background:linear-gradient(180deg,#eceef1 0%,#f4f5f7 55%,#e3e6ea 100%)}
.contact-sub{top:3582px;font-size:15px;color:var(--ink)}
.field{position:absolute;background:var(--white);border:1px solid #c9ccd1;font-size:14px;color:var(--ink);padding:0 17px;display:flex;align-items:center}
.field.msg{align-items:flex-start;padding-top:15px}
.submit{position:absolute;top:3859px;left:520px;width:161px;height:48px;background:var(--blue);color:var(--white);font-family:"Montserrat",sans-serif;font-size:18px;font-weight:500;display:flex;align-items:center;justify-content:center}

/* footer */
.footer{top:3974px;left:0;width:1200px;height:81px;background:var(--footer)}
.copy{top:4004px;font-size:13.5px;color:var(--white)}
</style>
</head>
<body>

<header class="abs site-header">
  <div class="abs brand">HALVIX <span style="color:var(--ink)">GROUP</span></div>
  <nav class="nav">
    <a class="active" style="left:436px">Home</a>
    <a style="left:530px">About Us</a>
    <a style="left:653px">Services</a>
    <a style="left:775px">Products</a>
    <a style="left:905px">News</a>
    <a style="left:1000px">Contact Us</a>
  </nav>
</header>

<section>
  <div class="abs hero" role="img" aria-label="Laboratory photo: gloved hands holding glass flasks over a periodic table"></div>
  <div class="abs hero-shade"></div>
  <h1 class="abs center hero-title">HALVIX GROUP</h1>
  <p class="abs center hero-sub">Sed ut perspiciatis unde omnis iste natus error sit</p>
  <a class="btn" style="top:535px;left:501px;width:198px;height:57px;font-size:19px">Read More</a>
  <div class="abs dots"><span></span><span class="on"></span><span></span></div>
</section>

<section>
  <div class="abs welcome"></div>
  <h2 class="abs center section-title" style="top:826px">Welcome to <span class="accent">Halvix Group</span></h2>
  <p class="abs welcome-text">Sed ut perspiciatis unde omnis iste natus error sit voluptatem accusantium doloremque laudantium, totam rem aperiam, eaque ipsa quae ab illo inventore veritatis et quasi architecto beatae vitae dicta sunt explicabo. Nemo enim ipsam voluptatem quia voluptas sit aspernatur aut odit aut fugit, sed quia consequuntur magni dolores eos accusantium doloremque qui ratione voluptatem sequi nesciunt.</p>
  <a class="btn" style="top:1032px;left:472px;width:256px;height:57px;font-size:13px">Click here for more info</a>
</section>

<section>
  <h2 class="abs center section-title" style="top:1192px;font-size:34px">Our <span class="accent">Products</span></h2>
  <div class="abs rule" style="top:1240px;left:570px"></div>

  <article class="card" style="left:112px">
    <div class="photo" role="img" aria-label="Handheld disinfecting sprayer"></div>
    <div class="name">PRODUCT 01</div>
    <div class="price">$1495</div>
    <a class="btn">View Details</a>
  </article>
  <article class="card" style="left:445px">
    <div class="photo" role="img" aria-label="Backpack disinfecting sprayer"></div>
    <div class="name">PRODUCT 02</div>
    <div class="price">$1495</div>
    <a class="btn">View Details</a>
  </article>
  <article class="card" style="left:778px">
    <div class="photo" role="img" aria-label="Wheeled cart disinfecting sprayer"></div>
    <div class="name">PRODUCT 03</div>
    <div class="price">$1495</div>
    <a class="btn">View Details</a>
  </article>
</section>

<section>
  <div class="feature-img" style="top:1829px;left:112px;background:linear-gradient(120deg,#c7ccd2 0%,#8f9aa5 40%,#5fa9c9 70%,#dfe3e7 100%)" role="img" aria-label="Technician in protective clothing working at a stainless steel mixing tank"></div>
  <h3 class="feature-title" style="top:1853px;left:642px">Sed ut perspiciatis<br>omnis iste natus error sit voluptatem</h3>
  <div class="feature-rule" style="top:1936px;left:645px"></div>
  <p class="feature-text" style="top:1957px;left:645px">Nemo enim ipsam voluptatem quia voluptas sit aspernatur aut odit aut fugit, sed quia consequuntur magni dolores eos qui ratione voluptatem sequi nesciunt. Neque porro quisq dolor sit amet, consectetur, adipisci velit</p>
  <a class="read-more" style="top:2101px;left:646px">READ MORE
    <svg width="14" height="14" viewBox="0 0 14 14"><circle cx="7" cy="7" r="5.8" fill="none" stroke="currentColor" stroke-width="1.8"/><path d="M6 4.5 8.5 7 6 9.5" fill="none" stroke="currentColor" stroke-width="1.8"/></svg></a>

  <h3 class="feature-title" style="top:2241px;left:124px">Sed ut perspiciatis<br>omnis iste natus error sit voluptatem</h3>
  <div class="feature-rule" style="top:2324px;left:127px"></div>
  <p class="feature-text" style="top:2345px;left:127px">Nemo enim ipsam voluptatem quia voluptas sit aspernatur aut odit aut fugit, sed quia consequuntur magni dolores eos qui ratione voluptatem sequi nesciunt. Neque porro quisq dolor sit amet, consectetur, adipisci velit</p>
  <a class="read-more" style="top:2490px;left:128px">READ MORE
    <svg width="14" height="14" viewBox="0 0 14 14"><circle cx="7" cy="7" r="5.8" fill="none" stroke="currentColor" stroke-width="1.8"/><path d="M6 4.5 8.5 7 6 9.5" fill="none" stroke="currentColor" stroke-width="1.8"/></svg></a>
  <div class="feature-img" style="top:2218px;left:600px;background:linear-gradient(110deg,#1d3d73 0%,#3f7fc0 40%,#c9d6e4 65%,#b99a2e 100%)" role="img" aria-label="Scientist in goggles examining a test tube of blue liquid"></div>
</section>

<section>
  <div class="abs band" role="img" aria-label="Blue-tinted photo of researchers working in a laboratory"></div>
  <h2 class="abs center band-title">Sed ut perspiciatis unde<br>natus error sit voluptatem accusantium</h2>
  <svg class="abs" style="top:2840px;left:550px" width="100" height="100" viewBox="0 0 100 100">
    <circle cx="50" cy="50" r="47" fill="none" stroke="#fff" stroke-width="5"/>
    <path d="M38 30 L70 50 L38 70 Z" fill="#fff"/>
  </svg>
</section>

<section>
  <div class="aud" style="left:112px">
    <div class="icon"><svg width="64" height="64" viewBox="0 0 64 64" fill="#fff"><rect x="8" y="22" width="48" height="32" rx="4"/><path d="M23 22v-7a3 3 0 0 1 3-3h12a3 3 0 0 1 3 3v7h-4v-6H27v6z"/><rect x="8" y="34" width="48" height="3" fill="#1a72c0"/></svg></div>
    <h3>Business</h3>
    <p>Sed ut perspiciatis unde omnis iste natus error sit voluptatem accusantium</p>
  </div>
  <div class="aud" style="left:359px">
    <div class="icon"><svg width="64" height="64" viewBox="0 0 64 64" fill="#fff"><rect x="14" y="12" width="36" height="44"/><rect x="29" y="17" width="6" height="16" fill="#1a72c0"/><rect x="24" y="22" width="16" height="6" fill="#1a72c0"/><rect x="27" y="43" width="10" height="13" fill="#1a72c0"/><rect x="8" y="55" width="48" height="3"/></svg></div>
    <h3>Hospital</h3>
    <p>Sed ut perspiciatis unde omnis iste natus error sit voluptatem accusantium</p>
  </div>
  <div class="aud" style="left:606px">
    <div class="icon"><svg width="70" height="64" viewBox="0 0 70 64" fill="#fff"><path d="M35 10 52 24H18z"/><rect x="20" y="24" width="30" height="30"/><rect x="4" y="32" width="16" height="22"/><rect x="50" y="32" width="16" height="22"/><rect x="30" y="40" width="10" height="14" fill="#1a72c0"/><rect x="8" y="37" width="8" height="5" fill="#1a72c0"/><rect x="54" y="37" width="8" height="5" fill="#1a72c0"/><circle cx="35" cy="31" r="3" fill="#1a72c0"/></svg></div>
    <h3>School District</h3>
    <p>Sed ut perspiciatis unde omnis iste natus error sit voluptatem accusantium</p>
  </div>
  <div class="aud" style="left:853px">
    <div class="icon"><svg width="64" height="64" viewBox="0 0 64 64" fill="#fff"><path d="M32 14 60 26 32 38 4 26z"/><path d="M16 32v12c0 5 32 5 32 0V32L32 39z"/><rect x="54" y="26" width="3" height="16"/></svg></div>
    <h3>Universities</h3>
    <p>Sed ut perspiciatis unde omnis iste natus error sit voluptatem accusantium</p>
  </div>
</section>

<section>
  <div class="abs contact" role="img" aria-label="Faded photo of an industrial skyline over water"></div>
  <h2 class="abs center section-title" style="top:3527px;font-size:34px">Contact <span class="accent">Us</span></h2>
  <p class="abs center contact-sub">Sed ut perspiciatis unde omnis iste natus error sit voluptatem accusantium doloremque laudantium</p>
  <div class="field" style="top:3635px;left:238px;width:357px;height:46px">First Name :</div>
  <div class="field" style="top:3635px;left:606px;width:358px;height:46px">Last Name :</div>
  <div class="field" style="top:3692px;left:238px;width:357px;height:46px">Email :</div>
  <div class="field" style="top:3692px;left:606px;width:358px;height:46px">Phone :</div>
  <div class="field msg" style="top:3749px;left:238px;width:726px;height:88px">Message :</div>
  <div class="submit">SUBMIT</div>
</section>

<footer>
  <div class="abs footer"></div>
  <p class="abs center copy">© Copyright 2020 Halvix Group.All rights reserved.</p>
</footer>

</body>
</html>
```